design a construction company business card

Design business card around our logo. Card must have all the typical info: name, title, address, phone, email, business name, etc. Somewhere on the card I would like to see our motto "Grounded in trust... Driven by good craft." Consider adding a splash of bright orange to the card to complement the blues and silvers/grays in the logo. We are open to metallic inks, textures, etc. We would like to see options on both light and dark backgrounds. The font in the logo is Euro Technic Extended Regular.

```html
<!DOCTYPE html>
<html lang="en">
<head>
<meta charset="utf-8">
<title>Halden Contracting – Business Card</title>
<link href="https://fonts.googleapis.com/css2?family=Open+Sans:wght@400;600;800&display=swap" rel="stylesheet">
<style>
  :root {
    --backdrop: #2a2a2a;
    --card: #2f2f30;
    --card-edge: #3a3a3b;
    --silver: #b9bcc0;
    --muted: #8c8f93;
    --text: #e6e7e9;
    --blue: #2f6fd6;
    --blue-deep: #1f4fb0;
  }
  * { margin: 0; padding: 0; box-sizing: border-box; }
  html, body {
    width: 1200px; height: 895px; overflow: hidden;
    background: var(--backdrop);
    font-family: "Open Sans", Arial, sans-serif;
  }
  .canvas {
    position: relative; width: 1200px; height: 895px;
  }
  .card {
    position: absolute; left: 260px; width: 680px; height: 388px;
    border-radius: 16px;
    background:
      repeating-linear-gradient(90deg, rgba(255,255,255,0.015) 0 2px, rgba(0,0,0,0.02) 2px 4px),
      linear-gradient(160deg, #353536 0%, var(--card) 55%, #2a2a2b 100%);
    border: 1px solid var(--card-edge);
    box-shadow: 0 14px 30px rgba(0,0,0,0.45);
  }
  .card--front { top: 40px; }
  .card--back { top: 467px; }

  .brand-name {
    font-weight: 600; letter-spacing: 0.12em; text-transform: uppercase;
    display: flex; align-items: center; gap: 14px; white-space: nowrap;
  }
  .brand-mark { width: 16px; height: 16px; border-radius: 50%; flex: none; }

  .card--front .brand-name {
    position: absolute; top: 150px; left: 0; right: 0; justify-content: center;
    font-size: 30px; color: var(--silver);
  }
  .card--front .brand-mark { background: var(--silver); }
  .tagline {
    position: absolute; top: 262px; left: 0; right: 0; text-align: center;
    font-size: 17px; color: var(--muted); letter-spacing: 0.02em;
  }

  .card--back .brand-name {
    position: absolute; top: 70px; right: 46px;
    font-size: 24px; color: var(--blue);
  }
  .card--back .brand-mark { background: var(--blue); }

  .contact {
    position: absolute; left: 56px; bottom: 44px; color: var(--text);
  }
  .contact__name {
    font-weight: 800; font-size: 30px; color: var(--blue); letter-spacing: 0.02em;
    text-transform: uppercase; line-height: 1.05;
  }
  .contact__title { font-size: 18px; margin-bottom: 16px; }
  .contact__address { font-size: 18px; line-height: 1.35; margin-bottom: 10px; }
  .contact__list { list-style: none; font-size: 18px; line-height: 1.5; }
  .contact__list li { display: flex; align-items: center; gap: 12px; }
  .contact__list svg { width: 18px; height: 18px; flex: none; }
</style>
</head>
<body>
<main class="canvas">

  <section class="card card--front" aria-label="Card front">
    <div class="brand-name"><span class="brand-mark"></span>Halden Contracting, Inc.</div>
    <p class="tagline">Grounded in trust... Driven by good craft</p>
  </section>

  <section class="card card--back" aria-label="Card back">
    <div class="brand-name"><span class="brand-mark"></span>Halden Contracting, Inc.</div>
    <div class="contact">
      <h1 class="contact__name">Marcus Reed</h1>
      <p class="contact__title">Founder &amp; CEO</p>
      <p class="contact__address">48 Harbour Road, Suite # B<br>Leeds, United Kingdom LS1 4AB</p>
      <ul class="contact__list">
        <li>
          <svg viewBox="0 0 24 24" aria-hidden="true"><path fill="var(--blue)" d="M6.6 10.8a15 15 0 0 0 6.6 6.6l2.2-2.2a1 1 0 0 1 1-.25 11.4 11.4 0 0 0 3.6.57 1 1 0 0 1 1 1V20a1 1 0 0 1-1 1A17 17 0 0 1 3 4a1 1 0 0 1 1-1h3.5a1 1 0 0 1 1 1c0 1.25.2 2.45.57 3.57a1 1 0 0 1-.25 1z"/></svg>
          123 555 0147
        </li>
        <li>
          <svg viewBox="0 0 24 24" aria-hidden="true"><rect x="2" y="5" width="20" height="14" rx="1.5" fill="var(--blue)"/><path d="M3 6l9 7 9-7" fill="none" stroke="var(--card)" stroke-width="1.6"/></svg>
          marcus.reed@haldenbuild.co.uk
        </li>
        <li>
          <svg viewBox="0 0 24 24" aria-hidden="true"><circle cx="12" cy="12" r="10" fill="var(--blue-deep)"/><path d="M2 12h20M12 2c3 3 3 17 0 20M12 2c-3 3-3 17 0 20" fill="none" stroke="var(--card)" stroke-width="1.3"/></svg>
          www.haldenbuild.co.uk
        </li>
      </ul>
    </div>
  </section>

</main>
</body>
</html>
```